Brookmere Osteopathy flyer

I want a clean clear DL flyer (but also want an A4 poster) promoting a new Osteopathic business in a semi rural area in Tasmania (Australia).
It can have pictures like the examples attached to show people what Osteopathy is (its like Chiropractic and physiotherapy).
I am the sole practioner and am male, so any pictures would be best to be a white male if possible.
I've attached some wording, you can use all, or none of it
I don't have a phone number for the business yet
info@brookmereosteopathy.example
www.brookmereosteopathy.example
Target Market(s)
Australians, from tradies, professionals, babies to retired people
Industry/Entity Type
Health
Look and feel

```html
<!DOCTYPE html>
<html lang="en">
<head>
<meta charset="utf-8">
<title>Brookmere Osteopathy flyer</title>
<link href="https://fonts.googleapis.com/css2?family=Poppins:wght@400;500;600;700;800&display=swap" rel="stylesheet">
<style>
  :root{
    --blue:#0b95d3;
    --orange:#f47f20;
    --navy:#050d4f;
    --ink:#111111;
    --text:#333333;
    --page:#e7e6e7;
    --white:#ffffff;
  }
  *{margin:0;padding:0;box-sizing:border-box}
  html,body{width:674px;height:1200px;overflow:hidden;background:var(--page);font-family:'Poppins',sans-serif}
  .flyer{position:absolute;left:53px;top:0;width:567px;height:1200px;background:var(--white);overflow:hidden}
  .brand{position:absolute;top:62px;left:0;width:100%;display:flex;flex-direction:column;align-items:center;gap:10px}
  .brand-dot{width:96px;height:96px;border-radius:50%;border:3px solid var(--blue)}
  .brand-name{font-weight:600;font-size:19px;color:var(--blue);letter-spacing:.5px}
  .headline{position:absolute;top:210px;left:0;width:100%;text-align:center;font-weight:800;font-size:37px;line-height:43px;letter-spacing:-1px}
  .headline .top{color:var(--blue)}
  .headline .bottom{color:var(--orange)}
  .intro{position:absolute;top:306px;left:0;width:100%;text-align:center;font-weight:500;font-size:16.5px;line-height:21px;color:var(--ink)}
  .hero{position:absolute;top:381px;left:0;width:567px;height:360px;background:linear-gradient(160deg,#f4f4f4 0%,#e4e4e2 45%,#d8d8d6 100%)}
  .hero-edge{position:absolute;top:378px;left:0}
  .spine-band{position:absolute;top:672px;left:0}
  .reasons-title{position:absolute;top:788px;left:0;width:100%;text-align:center}
  .reasons-title .small{display:block;font-weight:600;font-size:19px;line-height:22px;color:var(--blue)}
  .reasons-title .large{display:block;font-weight:700;font-size:29px;line-height:32px;color:var(--orange);letter-spacing:-.3px}
  .conditions{position:absolute;top:865px;list-style:none}
  .conditions.left{left:59px}
  .conditions.right{left:310px}
  .conditions li{display:flex;align-items:flex-start;gap:9px;font-size:14.5px;line-height:19px;color:var(--text);margin-bottom:7px}
  .conditions li .icon{flex:none;width:24px;height:24px;border-radius:50%;background:var(--blue);border:2.5px solid var(--orange);margin-top:-2px}
  .method{position:absolute;top:1026px;left:0;width:100%;height:68px;background:var(--orange);color:var(--white);text-align:center;font-weight:600;font-size:13.4px;line-height:18.5px;padding-top:6px}
  .contact{position:absolute;top:1102px;left:0;width:100%;height:98px;background:var(--navy);color:var(--white)}
  .contact-item{position:absolute;display:flex;align-items:center;gap:10px;font-size:11.5px;line-height:14px}
  .contact-item svg{flex:none}
</style>
</head>
<body>
<main class="flyer">
  <header class="brand">
    <span class="brand-dot"></span>
    <span class="brand-name">Brookmere Osteopathy</span>
  </header>

  <h1 class="headline"><span class="top">STRUGGLING WITH</span><br><span class="bottom">PAIN OR DISCOMFORT?</span></h1>

  <p class="intro">Our osteopaths treat a wide range of conditions<br>from back pain to sports injuries&nbsp; to help<br>you feel your best.</p>

  <div class="hero" role="img" aria-label="Photo of an osteopath treating a patient lying on their side on a treatment table"></div>
  <svg class="hero-edge" width="567" height="20" viewBox="0 0 567 20"><path d="M0 0 H567 V3 Q283 22 0 3 Z" fill="#ffffff"/></svg>
  <svg class="spine-band" width="567" height="100" viewBox="0 0 567 100"><path d="M0 96 C120 80 200 40 300 60 C400 80 480 60 567 30 L567 46 C480 80 400 100 300 80 C200 62 120 100 0 100 Z" fill="var(--blue)"/><rect x="0" y="100" width="567" height="0" fill="#fff"/></svg>

  <h2 class="reasons-title"><span class="small">COMMON REASONS PEOPLE</span><span class="large">VISIT AN OSTEOPATH</span></h2>

  <ul class="conditions left">
    <li><span class="icon"></span>Back / neck pain</li>
    <li><span class="icon"></span>Headaches / migraines</li>
    <li><span class="icon"></span>Joint and muscle pain</li>
    <li><span class="icon"></span>Pregnancy-related<br>discomfort</li>
    <li><span class="icon"></span>Disc related issues</li>
  </ul>
  <ul class="conditions right">
    <li><span class="icon"></span>Sciatica</li>
    <li><span class="icon"></span>Plantar fasciitis</li>
    <li><span class="icon"></span>Tendonitis / Bursitis</li>
    <li><span class="icon"></span>Adhesive capsulitis<br>(frozen shoulder)</li>
    <li><span class="icon"></span>Tennis / Golfers elbow</li>
  </ul>

  <p class="method">Osteopaths use a combination of joint manipulation,targeted<br>deep tissue massage and stretching to improve function,<br>relieve pain and support the body’s ability to heal itself.</p>

  <footer class="contact">
    <div class="contact-item" style="left:59px;top:22px">
      <svg width="18" height="18" viewBox="0 0 18 18"><circle cx="9" cy="9" r="9" fill="#fff"/><path d="M6 4.5 L7.6 6.8 L6.8 8 Q8 10.4 10 11.2 L11.2 10.4 L13.5 12 L12.5 13.6 Q8.5 14 5.6 10 Q4 7 5 5 Z" fill="var(--navy)"/></svg>
      <span>555 - 014 - 2290</span>
    </div>
    <div class="contact-item" style="left:59px;top:53px">
      <svg width="18" height="18" viewBox="0 0 18 18"><circle cx="9" cy="9" r="9" fill="#fff"/><rect x="4.5" y="6" width="9" height="6.5" fill="none" stroke="var(--navy)" stroke-width="1.2"/><path d="M4.5 6 L9 9.8 L13.5 6" fill="none" stroke="var(--navy)" stroke-width="1.2"/></svg>
      <span>info@brookmereosteopathy.example</span>
    </div>
    <div class="contact-item" style="left:310px;top:17px">
      <svg width="18" height="18" viewBox="0 0 18 18"><circle cx="9" cy="9" r="9" fill="#fff"/><path d="M9 3.5 A3.6 3.6 0 0 1 12.6 7.1 C12.6 9.6 9 14 9 14 C9 14 5.4 9.6 5.4 7.1 A3.6 3.6 0 0 1 9 3.5 Z" fill="var(--navy)"/><circle cx="9" cy="7.2" r="1.4" fill="#fff"/></svg>
      <span>24 Willow Bend road,<br>Brookmere</span>
    </div>
    <div class="contact-item" style="left:310px;top:53px">
      <svg width="18" height="18" viewBox="0 0 18 18"><circle cx="9" cy="9" r="9" fill="#fff"/><circle cx="9" cy="9" r="5" fill="none" stroke="var(--navy)" stroke-width="1.1"/><ellipse cx="9" cy="9" rx="2.2" ry="5" fill="none" stroke="var(--navy)" stroke-width="1.1"/><path d="M4 9 H14" stroke="var(--navy)" stroke-width="1.1"/></svg>
      <span>www.brookmereosteopathy.example</span>
    </div>
  </footer>
</main>
</body>
</html>
```